Lone Star Wetland Flora Stewardship Guild

We need to design the home page of this new website. We would like a fun website design for provides as a resource for members and information for potential members.
Please design so that we can see a portion of background on each side on the website.
I just need the final design files psd no coding needed.
Attached is their logo (colors are not 100% set in stone either so can mess with those as I did in the quick mockup attached)
Attached is a pdf newsletter they send out, you can get a feel for them and what they are about. The design is crappy and we are here to fix that going forward and we are starting with the website.
Here are some quick example websites (design style is open)
- I attached a quick mockup i did just for a content visual but by all means do what you want.
- http://www.brightpathleaders.example/
- http://www.civicunityhub.example/
- http://preview.webskinvault.example/show.php?cat=layouts&host=skinbazaar&temp=novaline
- http://www.meadowkeep.example/
- http://www.urbangleaners.example/
- http://www.projectcozyknit.example/
here are some of the other chapters website (pretty bad!)
and here are some of the others:
- http://www.dwrvcs.example/
- http://kwfg.example/
- http://www.blvcg.example/
Content Items that need to be included:
1. Logo
2. Menu - home, about, members, resources, events, membership, contact
3. Become a member - button or action
4. social links - chatterloop, workweave, clipstream
5. banner - that needs to explain their purpose "Promoting environmental stewardship through operations, research, education and outreach" (or this can be worked into the design)
6. Upcoming event (s)
7. Advertisement - members can place an ad on the website, this can be a placeholder for now
8. newsletter signup
9. advertise with us - this link can be in the footer
30-60 years of age, succesfull (household budgets of 120K+ men and women that live in texas.
Education

```html
<!DOCTYPE html>
<html lang="en">
<head>
<meta charset="utf-8">
<title>Lone Star Wetland Flora Stewardship Guild</title>
<link rel="stylesheet" href="https://fonts.googleapis.com/css2?family=Open+Sans:wght@400;600;700&display=swap">
<style>
:root{
  --red:#d63a4c;
  --red-dark:#c12a3c;
  --ink:#3a3a3a;
  --muted:#7a7a7a;
  --soft:#9a9a9a;
  --page:#ffffff;
  --backdrop:#e6e6e6;
  --nav:#f2f2f2;
  --footer:#f4f4f4;
  --bar:#2e3035;
  --line:#dcdcdc;
}
*{box-sizing:border-box;margin:0;padding:0}
html,body{width:828px;height:1200px;overflow:hidden}
body{background:var(--backdrop);font-family:"Open Sans",Arial,sans-serif;color:var(--ink);position:relative}
.page{position:absolute;left:25px;top:0;width:778px;height:1200px;background:var(--page);box-shadow:0 0 6px rgba(0,0,0,.12)}
a{color:inherit;text-decoration:none}

/* header */
.brand{position:absolute;left:24px;top:30px;display:flex;align-items:center;gap:8px}
.brand-dot{width:14px;height:14px;border-radius:50%;background:var(--red)}
.brand-name{font-size:13px;font-weight:700;color:var(--ink);line-height:1.25;width:170px}
.utility{position:absolute;right:61px;top:11px;display:flex;align-items:center;font-size:10px;color:var(--muted)}
.utility a{display:flex;align-items:center;gap:5px}
.utility .sep{width:1px;height:12px;background:var(--line);margin:0 14px}
.join{position:absolute;left:569px;top:70px;width:186px;height:28px;background:var(--red);color:#fff;font-size:11px;padding:6px 0 0 14px}
.join b{font-weight:700}
.join svg{position:absolute;right:10px;bottom:0}

/* nav */
.nav{position:absolute;left:0;top:110px;width:778px;height:45px;background:var(--nav);display:flex;border-bottom:4px solid var(--red);box-sizing:content-box}
.nav a{height:45px;display:flex;align-items:center;justify-content:center;font-size:11px;color:var(--ink);border-right:1px solid #e2e2e2}
.nav a.current{background:var(--red);color:#fff}

/* hero */
.hero{position:absolute;left:0;top:159px;width:778px;height:388px;background:linear-gradient(180deg,#7fb2e6 0%,#bfd9f0 28%,#5b8c3c 38%,#4f7a34 47%,#6f8a76 52%,#8a9a6a 70%,#a6ad5c 100%)}
.hero-arrow{position:absolute;top:153px;width:44px;height:44px;background:#fff;display:flex;align-items:center;justify-content:center}
.hero-arrow.prev{left:0}
.hero-arrow.next{right:0}
.hero-caption{position:absolute;left:0;top:249px;width:426px;height:58px;background:rgba(255,255,255,.88);clip-path:polygon(0 0,396px 0,100% 100%,0 100%);border-bottom:4px solid var(--red);padding:12px 0 0 18px;font-size:12.5px;line-height:15px;color:var(--ink)}

/* content */
.col-title{position:absolute;font-size:16px;color:var(--ink);border-bottom:1px solid var(--line);padding-bottom:3px}
.col-title::after{content:"";position:absolute;left:0;bottom:-2px;height:3px;background:var(--red)}
.about-title{left:25px;top:577px;width:211px}
.about-title::after{width:98px}
.events-title{left:290px;top:577px;width:232px}
.events-title::after{width:97px}
.about-text{position:absolute;left:25px;top:622px;width:211px;font-size:9.5px;line-height:14px;color:#555;text-align:justify}
.about-text p+p{margin-top:14px}
.event{position:absolute;left:290px;width:232px;display:flex;gap:13px;padding-bottom:9px;border-bottom:1px solid var(--line)}
.event:last-of-type{border-bottom:none}
.thumb{width:58px;height:44px;flex:none;border:1px solid #ddd;padding:2px;background:#fff}
.thumb span{display:block;width:100%;height:100%}
.event-text{font-size:9.5px;line-height:13px;color:#555;padding-top:3px}
.event-text.feature{font-size:10px;line-height:12px;padding-top:6px}
.event-text em{font-style:normal;color:var(--red)}
.more{position:absolute;top:821px;width:58px;height:23px;background:var(--red);color:#fff;font-size:11px;display:flex;align-items:center;justify-content:center;box-shadow:0 2px 0 var(--red-dark)}
.ad{position:absolute;left:559px;top:588px;width:199px;height:257px;background:linear-gradient(180deg,#2f7fb4 0%,#1e5f8f 45%,#e9e9e9 80%,#e9e9e9 100%)}

/* newsletter */
.signup{position:absolute;left:0;top:886px;width:778px;height:57px;background:var(--red)}
.signup-label{position:absolute;left:0;top:0;width:277px;height:57px;background:var(--red-dark);clip-path:polygon(0 0,262px 0,100% 50%,262px 100%,0 100%);color:#fff;font-size:13.5px;padding:20px 0 0 27px}
.signup-field{position:absolute;left:311px;top:18px;width:330px;height:21px;background:#fff;border:1px solid #bbb;font-size:8px;color:#666;padding:4px 6px}
.signup-send{position:absolute;left:666px;top:18px;width:83px;height:22px;background:#2a2a2a;color:#fff;font-size:11px;display:flex;align-items:center;justify-content:center;box-shadow:0 2px 0 #111}

/* footer */
.footer{position:absolute;left:0;top:943px;width:778px;height:207px;background:var(--footer)}
.foot-col{position:absolute;top:34px}
.foot-title{font-size:13.5px;color:var(--ink);border-bottom:1px solid var(--line);padding-bottom:2px;position:relative;margin-bottom:14px}
.foot-title::after{content:"";position:absolute;left:0;bottom:-2px;height:3px;background:var(--red);width:var(--bar-w)}
.foot-list{list-style:none;font-size:8.5px;line-height:14.5px;color:var(--soft);text-transform:uppercase}
.foot-list .active{color:var(--red)}
.social li{display:flex;align-items:center;gap:6px;margin-bottom:5px;line-height:14px}
.social i{width:13px;height:13px;border-radius:50%;background:#555;display:block}
.advertise{display:inline-block;margin-top:12px;background:var(--red-dark);color:#fff;font-size:10px;padding:3px 8px}
.address{font-size:9px;line-height:13.3px;color:var(--soft);width:170px}
.bottom-bar{position:absolute;left:0;top:1150px;width:778px;height:50px;background:var(--bar);color:#8a8c90;font-size:8.5px;display:flex;align-items:center;justify-content:center}
</style>
</head>
<body>
<div class="page">

  <header>
    <a class="brand" href="#"><span class="brand-dot"></span><span class="brand-name">Lone Star Wetland Flora Stewardship Guild</span></a>
    <div class="utility">
      <a href="#"><svg width="9" height="11" viewBox="0 0 9 11"><rect x="0" y="4.5" width="9" height="6.5" fill="#777"/><path d="M2 4.5V3a2.5 2.5 0 0 1 5 0v1.5" fill="none" stroke="#777" stroke-width="1.4"/></svg>LOGIN</a>
      <span class="sep"></span>
      <a href="#"><svg width="12" height="12" viewBox="0 0 12 12"><circle cx="6" cy="6" r="5.3" fill="none" stroke="#777"/><path d="M4 3.3l1 1.4-.6.8c.5 1 1.1 1.6 2.1 2.1l.8-.6 1.4 1-.6 1C6.3 8.8 3.2 5.7 3.3 3.9z" fill="#777"/></svg>CONTACT US</a>
    </div>
    <a class="join" href="#">BECOME A <b>MEMBER</b>
      <svg width="46" height="52" viewBox="0 0 46 52"><circle cx="22" cy="13" r="10" fill="#222"/><path d="M4 52c0-16 8-24 18-24s18 8 18 24z" fill="#222"/><circle cx="35" cy="40" r="9" fill="#222" stroke="#fff" stroke-width="1.5"/><path d="M35 35v10M30 40h10" stroke="#fff" stroke-width="2.2"/></svg>
    </a>
  </header>

  <nav class="nav">
    <a class="current" href="#" style="width:91px">HOME</a>
    <a href="#" style="width:96px">ABOUT</a>
    <a href="#" style="width:104px">MEMBERS</a>
    <a href="#" style="width:118px">RESOURCES</a>
    <a href="#" style="width:109px">EVENTS</a>
    <a href="#" style="width:129px">MEMBERSHIP</a>
    <a href="#" style="width:131px;border-right:none">CONTACT</a>
  </nav>

  <section class="hero" role="img" aria-label="Photo of a calm lake covered in water lilies, framed by green trees under a blue sky">
    <a class="hero-arrow prev" href="#" aria-label="Previous slide"><svg width="14" height="26" viewBox="0 0 14 26"><path d="M12 2L2 13l10 11" fill="none" stroke="#555" stroke-width="2"/></svg></a>
    <a class="hero-arrow next" href="#" aria-label="Next slide"><svg width="14" height="26" viewBox="0 0 14 26"><path d="M2 2l10 11L2 24" fill="none" stroke="#555" stroke-width="2"/></svg></a>
    <div class="hero-caption">PROMOTING ENVIRONMENTAL STEWARDSHIP<br>THROUGH OPERATIONS, RESEARCH, EDUCATION AND OUTREACH</div>
  </section>

  <h2 class="col-title about-title">About&nbsp; LSWFSG</h2>
  <div class="about-text">
    <p>The Lone Star Wetland Flora Stewardship Guild, Inc. is an organization of scientists, educators, students, commercial pesticide applicators, administrators, and concerned individuals interested in the management and study of aquatic plants.</p>
    <p>The membership reflects a diversity of federal, state, and local agencies; universities and colleges around the world; corporations; and small businesses.</p>
  </div>
  <a class="more" href="#" style="left:26px">More</a>

  <h2 class="col-title events-title">Upcoming Events</h2>
  <div class="event" style="top:622px">
    <div class="thumb"><span role="img" aria-label="Event venue mark" style="background:#f1f1f1"></span></div>
    <div class="event-text feature">2014 LSWFSG CONFERENCE<br>OCTOBER 12-2014<br><em>BLUEBONNET BEND RANCH</em></div>
  </div>
  <div class="event" style="top:687px">
    <div class="thumb"><span role="img" aria-label="Photo of lily pads on a pond" style="background:linear-gradient(180deg,#6b8a4a,#8b9a55)"></span></div>
    <div class="event-text">Lorem ipsum dolor sit amet, consectetur adipisicing elit, sed do eiusmod tempor incididunt ut labore et dolore</div>
  </div>
  <div class="event" style="top:754px">
    <div class="thumb"><span role="img" aria-label="Photo of a tree-lined pond" style="background:linear-gradient(180deg,#5d8a3a,#7c9a6a)"></span></div>
    <div class="event-text">Lorem ipsum dolor sit amet, consectetur adipisicing elit, sed do eiusmod tempor incididunt ut labore et dolore</div>
  </div>
  <a class="more" href="#" style="left:291px">More</a>

  <aside class="ad" role="img" aria-label="Member advertisement: algaecide product containers on a blue background above the advertiser's name"></aside>

  <section class="signup">
    <div class="signup-label">SUBSCRIBE TO OUR NEWSLETTER</div>
    <div class="signup-field">Enter your email :</div>
    <a class="signup-send" href="#">SUBMIT</a>
  </section>

  <footer class="footer">
    <div class="foot-col" style="left:34px;width:118px">
      <h3 class="foot-title" style="--bar-w:77px">NAVIGATION</h3>
      <ul class="foot-list">
        <li class="active">Home</li><li>About</li><li>Members</li><li>Resources</li><li>Events</li><li>Membership</li><li>Contact</li>
      </ul>
    </div>
    <div class="foot-col" style="left:206px;width:123px">
      <h3 class="foot-title" style="--bar-w:91px">FOR MEMBERS</h3>
      <ul class="foot-list">
        <li>Forums</li><li>Promotions</li><li>Sign in</li><li>News</li>
      </ul>
      <a class="advertise" href="#">Advertise with us</a>
    </div>
    <div class="foot-col" style="left:393px;width:122px">
      <h3 class="foot-title" style="--bar-w:74px">FOLLOW US</h3>
      <ul class="foot-list social">
        <li><i></i>Chatterloop</li><li><i></i>Workweave</li><li><i></i>Clipstream</li>
      </ul>
    </div>
    <div class="foot-col" style="left:577px;width:164px">
      <h3 class="foot-title" style="--bar-w:96px">OUR LOCATION</h3>
      <p class="address">Lone Star Wetland Flora Stewardship Guild Address<br>Attn: Mara Quill, Treasurer<br>P.O. Box 418<br>Cedar Hollow, Texas 78000<br>Email: mquill@lswfsg.example</p>
    </div>
  </footer>

  <div class="bottom-bar">Copyright © 2014 | Privacy Policy, All Rights Reserved</div>
</div>
</body>
</html>
```